Modern Business Card

Modern professional business card with more than just logo and demographic info. Something memorable.

We are a trendy/modern chiropractic group with an emphasis on neurology, hence the minimalist-type brain logo. We want to convey that modern and technical aspect with professionalism and the elite nature of our practice environment.

```html
<!DOCTYPE html>
<html lang="en">
<head>
<meta charset="utf-8">
<title>Meridian Chiropractic — Business Card</title>
<link href="https://fonts.googleapis.com/css2?family=Cinzel:wght@400&family=Roboto:wght@400&display=swap" rel="stylesheet">
<style>
  :root {
    --brand-blue: #4a80c2;
    --paper: #ffffff;
    --page: #ffffff;
    --ink-grey: #6b6b6b;
    --rule-grey: #e2e2e2;
    --icon-blue: #4a80c2;
  }
  * { margin: 0; padding: 0; box-sizing: border-box; }
  html, body { width: 1200px; height: 1200px; overflow: hidden; background: var(--page); }
  .canvas { position: relative; width: 1200px; height: 1200px; }

  .card { position: absolute; overflow: hidden; }
  .card-front {
    left: 232px; top: 173px; width: 705px; height: 407px;
    background: var(--paper);
    outline: 1px solid #ececec;
  }
  .card-back {
    left: 231px; top: 628px; width: 702px; height: 401px;
    background: var(--brand-blue);
  }

  /* front: brand band */
  .brand-band {
    position: absolute; left: 0; top: 168px; width: 364px; height: 73px;
    background: var(--brand-blue);
  }
  .brand-dot {
    position: absolute; left: 50px; top: -4px; width: 81px; height: 81px;
    border-radius: 50%; background: var(--paper);
  }
  .wordmark {
    position: absolute; font-family: "Cinzel", serif; font-weight: 400;
    color: var(--paper); line-height: 1; white-space: nowrap;
  }
  .wordmark .line-main { display: block; }
  .wordmark .line-sub { display: block; }
  .brand-band .wordmark { left: 148px; top: 12px; }
  .brand-band .line-main { font-size: 33px; letter-spacing: 0.5px; }
  .brand-band .line-sub { font-size: 19.5px; margin-top: 2px; letter-spacing: 0.3px; }

  /* front: contact column */
  .column-divider {
    position: absolute; left: 364px; top: 57px; width: 10px; height: 296px;
    background: linear-gradient(to right, rgba(0,0,0,0.08), rgba(0,0,0,0));
  }
  .person-name {
    position: absolute; left: 394px; top: 62px;
    font-family: "Roboto", sans-serif; font-size: 33px; color: var(--brand-blue);
  }
  .person-title {
    position: absolute; left: 394px; top: 101px;
    font-family: "Roboto", sans-serif; font-size: 20px; color: var(--ink-grey);
  }
  .contact-list { position: absolute; left: 365px; top: 0; width: 293px; list-style: none; }
  .contact-item {
    position: absolute; left: 0; width: 293px;
    font-family: "Roboto", sans-serif; font-size: 19px; color: var(--ink-grey);
    line-height: 24px;
  }
  .contact-item svg { position: absolute; left: 27px; top: 3px; width: 18px; height: 18px; fill: var(--icon-blue); }
  .contact-item span { position: absolute; left: 63px; top: 0; white-space: nowrap; }
  .contact-rule { position: absolute; left: 365px; width: 293px; height: 2px; background: var(--rule-grey); }

  /* back */
  .back-lockup { position: absolute; left: 110px; top: 150px; height: 110px; }
  .back-lockup .brand-dot { left: 0; top: 0; width: 110px; height: 110px; }
  .back-lockup .wordmark { left: 142px; top: 6px; }
  .back-lockup .line-main { font-size: 66px; letter-spacing: 1px; }
  .back-lockup .line-sub { font-size: 38px; margin-top: 4px; letter-spacing: 0.5px; }
</style>
</head>
<body>
<div class="canvas">

  <section class="card card-front" aria-label="Card front">
    <div class="brand-band">
      <div class="brand-dot"></div>
      <div class="wordmark">
        <span class="line-main">MERIDIAN</span>
        <span class="line-sub">CHIROPRACTIC</span>
      </div>
    </div>

    <div class="column-divider"></div>
    <div class="person-name">Dorian Hale</div>
    <div class="person-title">President</div>

    <ul class="contact-list">
      <li class="contact-item" style="top:145px">
        <svg viewBox="0 0 24 24"><path d="M6.6 10.8a15.1 15.1 0 0 0 6.6 6.6l2.2-2.2c.3-.3.7-.4 1-.2 1.1.4 2.3.6 3.6.6.6 0 1 .4 1 1V20c0 .6-.4 1-1 1A17 17 0 0 1 3 4c0-.6.4-1 1-1h3.5c.6 0 1 .4 1 1 0 1.3.2 2.5.6 3.6.1.3 0 .7-.2 1z"/></svg>
        <span>012 3456 7890</span>
      </li>
      <li class="contact-item" style="top:181px">
        <svg viewBox="0 0 24 24"><path d="M2 5h18v8.5a5 5 0 0 0-7 5.5H2zm2 2v.3l7 4.6 7-4.6V7l-7 4.4z"/><circle cx="18.5" cy="18.5" r="4.5"/><path d="M16.3 18.6l1.5 1.5 2.7-2.9" stroke="#fff" stroke-width="1.4" fill="none"/></svg>
        <span>info@yourmail.com</span>
      </li>
      <li class="contact-item" style="top:215px">
        <svg viewBox="0 0 24 24"><path d="M12 2a10 10 0 1 0 0 20 10 10 0 0 0 0-20zm0 1.8c1 1.1 1.9 3 2.2 5.2H9.8c.3-2.2 1.2-4.1 2.2-5.2zM9.6 10.8h4.8a18 18 0 0 1 0 2.4H9.6a18 18 0 0 1 0-2.4zM3.9 10.8h3.9a20 20 0 0 0 0 2.4H3.9a8 8 0 0 1 0-2.4zm12.3 0h3.9a8 8 0 0 1 0 2.4h-3.9a20 20 0 0 0 0-2.4zM9.8 15h4.4c-.3 2.2-1.2 4.1-2.2 5.2-1-1.1-1.9-3-2.2-5.2zM4.6 9A8.2 8.2 0 0 1 9 4.3 13 13 0 0 0 8 9zm11.4 0a13 13 0 0 0-1-4.7A8.2 8.2 0 0 1 19.4 9zM4.6 15H8a13 13 0 0 0 1 4.7A8.2 8.2 0 0 1 4.6 15zm11.4 0h3.4a8.2 8.2 0 0 1-4.4 4.7 13 13 0 0 0 1-4.7z"/></svg>
        <span>www.yourwebside.com</span>
      </li>
      <li class="contact-item" style="top:256px">
        <svg viewBox="0 0 24 24"><path d="M7 3h10v4H7zM4 8h16a2 2 0 0 1 2 2v6h-4v-3H6v3H2v-6a2 2 0 0 1 2-2zm3 6h10v7H7z"/></svg>
        <span>00000000051</span>
      </li>
      <li class="contact-item" style="top:296px">
        <svg viewBox="0 0 24 24" style="top:6px;height:21px"><path d="M12 2a7 7 0 0 0-7 7c0 5.2 7 13 7 13s7-7.8 7-13a7 7 0 0 0-7-7zm0 9.5A2.5 2.5 0 1 1 12 6.5a2.5 2.5 0 0 1 0 5z"/></svg>
        <span>012 Physical Address 000<br>United State 5551</span>
      </li>
    </ul>

    <div class="contact-rule" style="top:175px"></div>
    <div class="contact-rule" style="top:210px"></div>
    <div class="contact-rule" style="top:248px"></div>
    <div class="contact-rule" style="top:286px"></div>
  </section>

  <section class="card card-back" aria-label="Card back">
    <div class="back-lockup">
      <div class="brand-dot"></div>
      <div class="wordmark">
        <span class="line-main">MERIDIAN</span>
        <span class="line-sub">CHIROPRACTIC</span>
      </div>
    </div>
  </section>

</div>
</body>
</html>
```